Business Card & Email Signature Design || Upmarket + Luxury

Rima Vale Honey, a New Zealand Manuka Honey company needs a Business Card & Email Signature design.

Our logo's are attached in Gold & Black versions, feel free to be creative with how you use the logo and it's patterns in your design.

Style:
- Looking for an Elegant, Luxurious, Upmarket feel.
- Black/Matte Black Card, Gold Foil, UV Embossing

Information to Add:

- Logo
- Company Name: Rima Vale Honey
- Name: Martin Holloway
- Title: Creative Director
- Phone: +64 2815 96 417
- Email: martin@rimavalehoney.example.nz
- Website: www.rimavalehoney.example.nz

- Socials: ***For email Signature Only***
- Facebook: https://www.facebook.com/rimavalehoney/
- Instagram: https://www.instagram.com/rimavalehoney/

Target Market(s)

Asia/Europe Luxury, Upmarket

Contact Information for Business Card

- Logo
- Name: Martin Holloway
- Phone: +64 2815 96 417

Font styles to use
Other font styles liked:
• Champagne & Limousines (Attached)

Requirements
Must have
• Business Card & Email Signature Design.

Looking for a Sleek, Luxury, Upmarket Design.

```html
<!DOCTYPE html>
<html lang="en">
<head>
<meta charset="utf-8">
<title>Rima Vale Honey — Business Card</title>
<link rel="stylesheet" href="https://fonts.googleapis.com/css2?family=Montserrat:wght@300;400;700&display=swap">
<style>
  :root {
    --page-bg: #1b1b1b;
    --card-black: #121212;
    --gold: #d4ad55;
    --gold-deep: #8a6a2c;
    --ink-white: #f2f2f2;
    --rule: #cfcfcf;
  }
  * { box-sizing: border-box; margin: 0; padding: 0; }
  html, body { width: 1200px; height: 780px; overflow: hidden; }
  body {
    background: var(--page-bg);
    font-family: "Montserrat", sans-serif;
    display: flex;
    align-items: center;
    justify-content: center;
    gap: 40px;
  }
  .card {
    width: 540px;
    height: 309px;
    background: var(--card-black);
    position: relative;
    box-shadow: 0 18px 40px rgba(0,0,0,.55);
  }
  /* Back side */
  .card-back .pattern-field {
    position: absolute;
    inset: 0;
    background: linear-gradient(215deg, #151515 0%, #1c1a14 45%, #3d3320 100%);
  }
  .card-back .corner-mark {
    position: absolute;
    right: 34px;
    top: 118px;
    font-size: 7px;
    letter-spacing: 2px;
    font-weight: 300;
    color: var(--gold);
    text-transform: uppercase;
  }
  /* Front side */
  .card-front .brand {
    position: absolute;
    left: 30px;
    top: 0;
    width: 250px;
    height: 100%;
    display: flex;
    flex-direction: column;
    align-items: center;
    justify-content: center;
    gap: 18px;
  }
  .brand-dot {
    width: 54px;
    height: 54px;
    border-radius: 50%;
    background: var(--gold);
  }
  .brand-name {
    font-weight: 300;
    font-size: 20px;
    letter-spacing: 5px;
    color: var(--gold);
    text-transform: uppercase;
    white-space: nowrap;
  }
  .divider {
    position: absolute;
    left: 298px;
    top: 92px;
    width: 1px;
    height: 132px;
    background: var(--rule);
  }
  .contact-block {
    position: absolute;
    left: 318px;
    top: 92px;
  }
  .person-name {
    font-weight: 700;
    font-size: 17px;
    letter-spacing: 1px;
    color: var(--gold);
    text-transform: uppercase;
  }
  .person-title {
    font-weight: 400;
    font-size: 11px;
    color: var(--ink-white);
    margin-top: 2px;
  }
  .contact-list {
    list-style: none;
    margin-top: 18px;
    display: flex;
    flex-direction: column;
    gap: 7px;
  }
  .contact-list li {
    display: flex;
    align-items: center;
    gap: 8px;
    font-size: 10px;
    color: var(--ink-white);
    white-space: nowrap;
  }
  .contact-icon { width: 11px; height: 11px; flex: none; }
</style>
</head>
<body>
  <section class="card card-back">
    <div class="pattern-field" role="img" aria-label="Repeating gold foil bee pattern fading across the black card"></div>
    <span class="corner-mark">Rima Vale Honey</span>
  </section>

  <section class="card card-front">
    <div class="brand">
      <span class="brand-dot"></span>
      <span class="brand-name">Rima Vale Honey</span>
    </div>
    <div class="divider"></div>
    <div class="contact-block">
      <h1 class="person-name">Martin Holloway</h1>
      <p class="person-title">Creative Director</p>
      <ul class="contact-list">
        <li>
          <svg class="contact-icon" viewBox="0 0 12 12"><circle cx="6" cy="6" r="6" fill="#d4ad55"/><path d="M4 3.2l1 1.3-.6.7a4 4 0 0 0 2.4 2.4l.7-.6 1.3 1-.6.9c-2.6-.2-4.9-2.5-5.1-5.1z" fill="#121212"/></svg>
          <span>+64 2815 96 417</span>
        </li>
        <li>
          <svg class="contact-icon" viewBox="0 0 12 12"><circle cx="6" cy="6" r="6" fill="#d4ad55"/><rect x="3" y="4" width="6" height="4.2" fill="#121212"/><path d="M3 4l3 2.3L9 4" stroke="#d4ad55" stroke-width=".7" fill="none"/></svg>
          <span>martin@rimavalehoney.example.nz</span>
        </li>
        <li>
          <svg class="contact-icon" viewBox="0 0 12 12"><circle cx="6" cy="6" r="6" fill="#d4ad55"/><circle cx="6" cy="6" r="3" fill="none" stroke="#121212" stroke-width=".8"/><path d="M3 6h6M6 3v6" stroke="#121212" stroke-width=".7"/></svg>
          <span>www.rimavalehoney.example.nz</span>
        </li>
      </ul>
    </div>
  </section>
</body>
</html>
```